Italian restaurant needs new site

Need to make our website better.

Must have reservation module

Must be able to sell wine tasting tours and wine pairing tours and intégrate with dunmo desk

Blog

Social media

Wandervane ranking and last review.
Updates

Number of Pages Required

1 page

Font styles to use
Serif

Requirements
Must have
• Reservation module
• Marketplace to buy wine pairings and gift certificates
• Wandervane review
• Kindlepost posts
• All info from old site

```html
<!DOCTYPE html>
<html lang="en">
<head>
<meta charset="utf-8">
<title>Vinalto Bistro – Italian Restaurant in Cabo San Lucas</title>
<link rel="stylesheet" href="https://fonts.googleapis.com/css2?family=Domine:wght@400;700&family=Lora:ital,wght@0,400;0,700;1,400&family=Yellowtail&display=swap">
<style>
:root{
  --red:#a3161c;
  --red-dark:#7e1015;
  --ink:#222;
  --muted:#666;
  --dark:#181716;
  --darker:#111010;
  --paper:#ffffff;
  --wood:#e4d0b1;
  --line:#d8d8d8;
  --teal:#2aa889;
}
*{box-sizing:border-box;margin:0;padding:0}
html,body{width:1200px;height:3432px;overflow:hidden}
body{font-family:"Lora",Georgia,serif;color:var(--ink);background:var(--paper);font-size:15px;line-height:1.5}

/* hero */
.hero{position:relative;height:760px;color:#fff}
.hero-photo{position:absolute;inset:0;background:radial-gradient(ellipse at 55% 35%,#6a3b22 0%,#3a2014 45%,#150c08 100%)}
.site-nav{position:absolute;top:0;left:0;right:0;height:90px;display:flex;align-items:center;justify-content:space-between;padding:0 60px;background:linear-gradient(#000a,#0000)}
.brand{display:flex;align-items:center;gap:12px;font-family:"Domine",serif;font-size:30px;font-weight:700;color:#fff}
.brand-dot{width:14px;height:14px;border-radius:50%;background:var(--red)}
.nav-links{display:flex;align-items:center;gap:30px;font-family:"Domine",serif;font-size:14px;font-weight:700;letter-spacing:1px}
.hero-copy{position:absolute;top:360px;left:0;right:0;text-align:center}
.hero-title{font-family:"Yellowtail",cursive;font-size:96px;line-height:1.05;font-weight:400}
.hero-sub{font-family:"Domine",serif;font-style:italic;font-size:24px;margin-top:8px}
.hero-text{width:600px;margin:14px auto 0;font-size:14px;color:#eee}
.hero-actions{display:flex;justify-content:center;gap:24px;margin-top:28px}
.btn{display:inline-block;font-family:"Domine",serif;font-weight:700;font-size:14px;letter-spacing:1px;padding:13px 30px;color:#fff;text-decoration:none}
.btn-ghost{border:2px solid #fff}
.btn-red{background:var(--red)}

/* offers */
.offers{display:flex;justify-content:center;gap:40px;padding:60px 0 0;height:400px}
.offer{width:280px;height:320px;position:relative;box-shadow:0 2px 10px #0003;border:6px solid #fff}
.offer-photo{position:absolute;inset:0}
.offer-label{position:absolute;left:0;right:0;bottom:26px;text-align:center;font-family:"Domine",serif;font-weight:700;font-size:16px;color:#fff;letter-spacing:.5px}
.offer-label span{background:#0008;padding:8px 16px;border-bottom:3px solid var(--red)}

/* about */
.about{padding:50px 150px 0;height:340px}
.section-title{display:flex;align-items:center;gap:24px;font-family:"Domine",serif;font-weight:700;font-size:26px;letter-spacing:.5px;justify-content:center;white-space:nowrap}
.section-title::before,.section-title::after{content:"";flex:1;height:1px;background:var(--line)}
.about p{font-size:14px;color:var(--muted);margin-top:18px}

/* menu */
.menu-band{position:relative;height:520px;color:#fff;overflow:hidden}
.menu-photo{position:absolute;inset:0;background:
  radial-gradient(ellipse 320px 260px at 88% 10%,#9b2226cc,#9b222600),
  radial-gradient(ellipse 200px 320px at 80% 60%,#c9b48a55,#c9b48a00),
  radial-gradient(ellipse 200px 220px at 10% 85%,#5a1a1c88,#5a1a1c00),
  radial-gradient(ellipse at 45% 50%,#2e2b29 0%,var(--darker) 75%)}
.menu-copy{position:absolute;top:110px;left:0;width:1000px;text-align:center}
.menu-script{font-family:"Yellowtail",cursive;font-size:96px;line-height:1;color:var(--red)}
.menu-kicker{font-family:"Domine",serif;font-weight:700;font-size:30px;letter-spacing:1px;margin-top:6px}
.menu-copy p{font-size:18px;margin:14px auto 26px;width:360px}

/* reservations */
.reserve{height:560px;padding:50px 0 0;background:linear-gradient(90deg,var(--wood),#efdec3 30%,var(--wood) 60%,#d9bf97);text-align:center}
.reserve h2{font-family:"Domine",serif;font-size:30px;font-weight:400;letter-spacing:1px}
.reserve .tagline{font-style:italic;font-size:15px;color:#555;border-bottom:1px solid #b99c74;display:inline-block;padding:0 60px 6px}
.reserve .lede{width:880px;margin:14px auto 0;font-size:13px;text-align:left;color:#444}
.booking{width:720px;margin:26px auto 0;background:#161412;padding:30px 36px 24px}
.field-row{display:flex;gap:14px;margin-bottom:14px}
.field{flex:1;height:34px;background:#fff;font-size:12px;color:#999;text-align:left;padding:8px 10px}
.field.note{flex:none;width:400px;height:96px}
.booking .btn{margin-top:8px}

/* widgets */
.widgets{display:flex;gap:40px;padding:40px 40px 0;height:580px}
.widget{flex:1;min-width:0}
.widget h3{font-family:"Domine",serif;font-weight:700;font-size:24px;border-bottom:1px solid var(--line);padding-bottom:8px;margin-bottom:14px}
.review-box{border:3px solid var(--teal);padding:14px;font-size:12px;height:420px}
.review-brand{display:flex;align-items:center;gap:8px;font-family:"Domine",serif;font-weight:700;font-size:18px;color:var(--teal);margin-bottom:10px}
.review-brand i{width:14px;height:14px;border-radius:50%;background:var(--teal);display:block}
.review-box h4{font-size:15px;margin:8px 0 2px}
.review-box .rank{color:var(--teal);font-weight:700}
.bubbles{display:flex;gap:4px;margin:4px 0}
.bubbles b{width:12px;height:12px;border-radius:50%;background:var(--teal)}
.review-box hr{border:0;border-top:1px solid var(--line);margin:12px 0}
.post{display:flex;gap:12px;padding:12px 0;border-bottom:1px solid var(--line)}
.post-thumb{width:100px;height:80px;background:linear-gradient(135deg,#5a3422,#c59a6b);flex:none}
.post-meta{font-size:11px;color:#999}
.post h4{font-family:"Domine",serif;font-size:14px;line-height:1.3}
.post p{font-size:11px;color:var(--muted)}
.see-all{text-align:center;font-family:"Domine",serif;font-size:12px;margin-top:14px;letter-spacing:1px}
.kp-box{border:1px solid var(--line);height:420px;font-size:12px}
.kp-cover{height:110px;background:linear-gradient(135deg,#3a1f14,#8a5430);position:relative}
.kp-name{position:absolute;left:110px;bottom:14px;color:#fff;font-family:"Domine",serif;font-weight:700;font-size:16px}
.kp-avatar{position:absolute;left:12px;bottom:-20px;width:84px;height:84px;background:#fff;border:3px solid #fff;display:flex;align-items:center;justify-content:center}
.kp-avatar i{width:40px;height:40px;background:var(--dark)}
.kp-body{padding:34px 12px 0}
.kp-grid{display:grid;grid-template-columns:repeat(5,1fr);gap:6px;margin-top:12px}
.kp-grid span{aspect-ratio:1;background:linear-gradient(135deg,#cfcfcf,#8f8f8f)}

/* footer */
.site-footer{height:272px;background:var(--dark);color:#ccc;padding:40px 60px 0;display:flex;align-items:flex-start;gap:60px;font-size:13px;position:relative}
.site-footer .brand{font-size:26px}
.footer-col h5{font-family:"Domine",serif;color:#fff;font-size:15px;margin-bottom:8px}
.footer-col li{list-style:none;line-height:1.6}
.map-wrap{margin-left:auto;text-align:right}
.map{width:200px;height:140px;background:linear-gradient(135deg,#e8e4dc,#c9d8c4);margin-left:auto}
.mini-links{margin-top:10px;display:flex;gap:14px;justify-content:flex-end;align-items:center}
.mini-links i{width:22px;height:22px;border-radius:50%;border:1px solid #888;display:inline-block}
.copyright{position:absolute;left:60px;bottom:24px;font-size:12px;color:#888}
</style>
</head>
<body>

<header class="hero">
  <div class="hero-photo" role="img" aria-label="Friends sharing wine and dinner at a candlelit table"></div>
  <nav class="site-nav">
    <div class="brand"><span class="brand-dot"></span>Vinalto Bistro</div>
    <div class="nav-links"><span>HOME</span><span>MENU</span><span>RESERVATIONS</span><span>BLOG</span><span>REVIEWS</span><span>CONTACT</span>
      <svg width="18" height="18" viewBox="0 0 24 24" fill="#fff"><path d="M3 4h3l2 11h11l2-8H7" stroke="#fff" stroke-width="2" fill="none"/><circle cx="9" cy="20" r="2"/><circle cx="18" cy="20" r="2"/></svg>
    </div>
  </nav>
  <div class="hero-copy">
    <h1 class="hero-title">Vinalto Bistro</h1>
    <div class="hero-sub">Italian Restaurant in Cabo San Lucas</div>
    <p class="hero-text">Vinalto Bistro sits in the heart of downtown, a warm room for fresh pasta, fine wine and long evenings. Gather friends and family for honest Italian food and a friendly table.</p>
    <div class="hero-actions"><a class="btn btn-ghost">EXPLORE MORE</a><a class="btn btn-red">RESERVATIONS</a></div>
  </div>
</header>

<section class="offers">
  <div class="offer"><div class="offer-photo" role="img" aria-label="Guest tasting red wine" style="background:linear-gradient(135deg,#6b3a28,#c49a74)"></div><div class="offer-label"><span>WINE TASTING TOURS</span></div></div>
  <div class="offer"><div class="offer-photo" role="img" aria-label="Glasses of wine paired with food" style="background:linear-gradient(135deg,#3a1a14,#9b4a36)"></div><div class="offer-label"><span>WINE PAIRING TOURS</span></div></div>
  <div class="offer"><div class="offer-photo" role="img" aria-label="Wine bottles in a gift box" style="background:linear-gradient(135deg,#8a6a44,#d9c3a0)"></div><div class="offer-label"><span>GIFT CERTIFICATE</span></div></div>
</section>

<section class="about">
  <h2 class="section-title">VINALTO BISTRO ITALIAN RESTAURANT IN CABO SAN LUCAS</h2>
  <p>Vinalto Bistro is located in the heart of downtown, across from the main plaza and a short walk from the marina. Our kitchen brings together the classic flavors of Italy and the fresh produce of Baja, served in a relaxed room with a European touch. Every plate is made from scratch each day, from hand rolled pasta to slow cooked sauces and wood fired breads, paired with a careful list of Italian and Mexican wines.</p>
  <p>Cabo locals and visitors alike come back for our friendly service and quiet terrace. Whether you are planning a romantic dinner, a family celebration or a private event, our team will make your evening simple and memorable.</p>
</section>

<section class="menu-band">
  <div class="menu-photo" role="img" aria-label="Dark table with a printed menu card, red checked cloth and wine bottles"></div>
  <div class="menu-copy">
    <div class="menu-script">Discover</div>
    <div class="menu-kicker">FULL MENU PDF</div>
    <p>Discover all our perfect Menu at Vinalto Bistro Cabo San Lucas with love!</p>
    <a class="btn btn-red">DISCOVER MENU</a>
  </div>
</section>

<section class="reserve">
  <h2>RESERVATIONS</h2>
  <div class="tagline">Reservations for Vinalto Bistro Cabo San Lucas</div>
  <p class="lede">Reservations at Vinalto Bistro are open every day of the week. For parties of more than eight guests please call us or send us a note and we will be glad to help. To book a table just fill in the form below; all online bookings are confirmed by email within a few hours. We look forward to seeing you soon.</p>
  <form class="booking">
    <div class="field-row"><div class="field">Name</div><div class="field">Email</div><div class="field">Phone</div></div>
    <div class="field-row"><div class="field">Date</div><div class="field">Time</div><div class="field">Number of guests</div></div>
    <div class="field-row"><div class="field note">Comments</div></div>
    <a class="btn btn-red">BOOK MY TABLE</a>
  </form>
</section>

<section class="widgets">
  <div class="widget">
    <h3>WANDERVANE REVIEW</h3>
    <div class="review-box">
      <div class="review-brand"><i></i>Wandervane</div>
      <h4>Vinalto Bistro</h4>
      <div class="rank">Wandervane Traveler Rating</div>
      <div class="bubbles"><b></b><b></b><b></b><b></b><b></b></div>
      <div>#4 of 320 restaurants in Cabo San Lucas</div>
      <hr>
      <h4>Most Recent Traveler Reviews</h4>
      <p>“Best pasta in town” – Jul 2</p>
      <p>“Lovely dinner with friends” – Jun 28</p>
      <p>“Great wine pairing night” – Jun 21</p>
      <p>“Warm service, superb food” – Jun 15</p>
      <hr>
      <p class="rank">Read reviews | Write a review</p>
    </div>
  </div>
  <div class="widget">
    <h3>BLOG POSTS</h3>
    <div class="post"><div class="post-thumb" role="img" aria-label="Blog photo"></div><div><div class="post-meta">by vinalto · 2 comments</div><h4>A summer evening of wine and pasta</h4><p>Our chef shares the dishes guests loved most this season... Read more</p></div></div>
    <div class="post"><div class="post-thumb" role="img" aria-label="Blog photo"></div><div><div class="post-meta">by vinalto · 4 comments</div><h4>Inside our new wine pairing tour</h4><p>Five wines, five plates and one long table by the terrace... Read more</p></div></div>
    <div class="post"><div class="post-thumb" role="img" aria-label="Blog photo"></div><div><div class="post-meta">by vinalto · 1 comment</div><h4>Fresh from the Baja market</h4><p>How local produce finds its way into our daily specials... Read more</p></div></div>
    <div class="see-all">SEE ALL BLOG</div>
  </div>
  <div class="widget">
    <h3>KINDLEPOST</h3>
    <div class="kp-box">
      <div class="kp-cover" role="img" aria-label="Restaurant cover photo"><div class="kp-avatar"><i></i></div><div class="kp-name">Vinalto Bistro<br><small style="font-weight:400;font-size:11px">1,440 likes</small></div></div>
      <div class="kp-body">
        <p>Be the first of your friends to like this page.</p>
        <div class="kp-grid"><span></span><span></span><span></span><span></span><span></span><span></span><span></span><span></span><span></span><span></span></div>
      </div>
    </div>
  </div>
</section>

<footer class="site-footer">
  <div class="brand"><span class="brand-dot"></span>Vinalto Bistro</div>
  <div class="footer-col"><h5>Quick Links</h5><ul><li>Home</li><li>Menu</li><li>Reservations</li><li>Blog</li><li>Reviews</li><li>Contact</li></ul></div>
  <div class="footer-col"><h5>Contact Us</h5><ul><li>Vinalto Bistro</li><li>Calle Olivo 18, Centro</li><li>Cabo San Lucas, Mexico</li><li>+52 000 555 0142</li><li>Open daily from 5 to 10 pm</li></ul></div>
  <div class="map-wrap">
    <div class="map" role="img" aria-label="Map showing the restaurant location"></div>
    <div class="mini-links"><span>Terms of Use</span><span>Privacy</span><span>Sitemap</span><i></i><i></i></div>
  </div>
  <div class="copyright">Copyright 2017 Vinalto Bistro</div>
</footer>

</body>
</html>
```